Website for data analytics startup

I have a landing page up at http://quenvo.io I need to expand this into a basic company website. I want something similar to this design: http://kelmarix.com/examples/carousel/

I need HTML and CSS for each of the designs, once they are approved. I need the following pages: home page, product, team, blog, and a design for the container of our demo application.

Our logo is attached and also available here: https://files.dravistore.net/quenvo.public/LOGO-colour.png I would like the website branding to match the logo.

I need a blog design with CSS that works with Tumblr.

Our app can be seen at http://demo.quenvo.io Please don't change the look of the network graph itself, only the surrounding content.

For CSS, I want you to use Bootstrap or Foundation as the starting point.

Target Market(s)

Sales and marketing, strategy

Industry/Entity Type

It Company

Coding

Coded - Design and coding required

Number of Pages Required

4 page

Font styles to use
Serif
Sans Serif

Requirements
Must have
• Clean, healthy appeal. Must work well with our logo. Blog page must integrate with Tumblr easily. Must use Bootstrap or Foundation for the starting point of the HTML/CSS.
Should not have
• Ugly crap, flash looking design. NO FLASH.

```html
<!DOCTYPE html>
<html lang="en">
<head>
<meta charset="utf-8">
<title>quenvo — Data analytics</title>
<link rel="stylesheet" href="https://fonts.googleapis.com/css2?family=Oswald:wght@300;400&family=Open+Sans:wght@400;600&display=swap">
<style>
:root{
  --sky:#5bbfea;
  --leaf:#7dc242;
  --lime:#9be05a;
  --navy:#0f4a5f;
  --ink:#555b5e;
  --mist:#eef0f0;
  --slate:#3d3f41;
  --white:#ffffff;
}
*{box-sizing:border-box;margin:0;padding:0}
html,body{width:819px;height:1200px;overflow:hidden;background:var(--white)}
body{position:relative;font-family:"Open Sans",Arial,sans-serif;color:var(--ink)}
.abs{position:absolute}
.display{font-family:"Oswald","Arial Narrow",sans-serif;font-weight:300}

/* hero */
.hero{left:0;top:0;width:819px;height:379px;overflow:hidden}
.hero-photo{position:absolute;inset:0;background:linear-gradient(160deg,#9aa3ab 0%,#7d8790 40%,#6a727a 70%,#a7adb2 100%)}
.hero-shade{position:absolute;inset:0;background:rgba(40,50,60,.25)}
.brand{left:66px;top:32px;font-family:"Oswald","Arial Narrow",sans-serif;font-weight:300;font-size:24px;line-height:30px;color:var(--white)}
.social{display:flex;gap:7px}
.social span{width:7px;height:7px;border-radius:50%;background:currentColor;display:block}
.social-top{right:66px;top:18px;color:var(--white)}
.nav{right:66px;top:45px;display:flex;gap:35px;font-family:"Oswald",sans-serif;font-size:11px;color:var(--white)}
.nav .active{color:var(--sky)}
.hero-title{left:0;width:819px;top:146px;text-align:center;font-size:21px;color:var(--white)}
.hero-sub{left:0;width:819px;top:198px;text-align:center;font-family:"Oswald",sans-serif;font-size:12.5px;color:var(--lime)}
.hero-btn{left:362px;top:241px;width:101px;height:27px;border:1.5px solid var(--white);color:var(--sky);font-size:9.5px;font-weight:600;display:flex;align-items:center;justify-content:center}
.dots{left:395px;top:355px;display:flex;gap:7px}
.dots span{width:5px;height:5px;background:var(--sky)}
.dots span:nth-child(2){background:var(--lime)}

/* what we do */
.section-title{left:0;width:819px;text-align:center;color:var(--sky);text-transform:uppercase}
.lead{left:150px;width:519px;text-align:center;font-size:7.4px;line-height:14.5px}
.feature{width:200px;text-align:center}
.feature-icon{width:52px;height:52px;border-radius:50%;background:var(--navy);margin:0 auto;display:flex;align-items:center;justify-content:center}
.feature-title{font-family:"Oswald",sans-serif;font-weight:300;color:var(--leaf);font-size:13px;margin-top:13px}
.feature-text{font-size:7.4px;line-height:14px;margin:6px auto 0;width:180px}
.read-more{font-size:7.6px;font-weight:600;color:var(--navy);margin-top:8px}

/* markets */
.markets{left:0;top:706px;width:819px;height:384px;background:var(--mist)}
.sub-title{font-family:"Oswald",sans-serif;font-weight:300;color:var(--leaf);font-size:15.5px;text-align:center}
.sub-text{font-size:7.4px;text-align:center}
.monitor{left:97px;top:868px;width:259px;height:200px}
.screen{position:absolute;left:0;top:0;width:259px;height:158px;background:#1c1c1c;border-radius:6px;padding:12px 14px}
.screen-view{width:100%;height:100%;background:linear-gradient(135deg,#e9f3e5,#ece4f6 55%,#e4eef5)}
.stand{position:absolute;left:109px;top:158px;width:40px;height:22px;background:linear-gradient(#c8c8c8,#7a7a7a)}
.base{position:absolute;left:64px;top:178px;width:130px;height:14px;border-radius:50%;background:#2a2a2a}
.form{left:490px;top:868px;width:196px;height:198px;background:var(--slate);padding:4px 3px}
.form-head{color:var(--white);font-size:7.6px;text-align:center;height:16px;line-height:16px}
.field{background:var(--white);height:21px;margin-top:5px;font-size:7.4px;color:#777;padding:0 14px;line-height:21px}
.field.tall{height:62px;line-height:20px}
.form-btn{margin-top:5px;height:27px;background:linear-gradient(#a4e27a,#72c44a);color:#2f4a1e;font-size:8.8px;text-align:center;line-height:27px;letter-spacing:.3px}

/* footer */
.footer-nav{left:0;width:819px;top:1112px;display:flex;justify-content:center;gap:45px;font-size:8px;color:var(--navy)}
.social-foot{left:378px;top:1144px;color:var(--navy)}
.copyright{left:0;width:819px;top:1167px;text-align:center;font-size:8.4px;color:var(--navy)}
</style>
</head>
<body>

<header class="hero abs">
  <div class="hero-photo" role="img" aria-label="Photo of a hand tapping a chart on a tablet held over an open ledger"></div>
  <div class="hero-shade"></div>
</header>
<div class="brand abs">quenvo</div>
<div class="social social-top abs"><span></span><span></span><span></span><span></span><span></span></div>
<nav class="nav abs">
  <span class="active">Home</span><span>About us</span><span>Services</span><span>Data analytics</span><span>Contact us</span>
</nav>
<h1 class="hero-title display abs">Without big data analytics, companies are blind and deaf</h1>
<p class="hero-sub abs">wandering out onto the Web like deer on a freeway.</p>
<div class="hero-btn abs">More details &nbsp;&gt;&gt;</div>
<div class="dots abs"><span></span><span></span><span></span></div>

<h2 class="section-title display abs" style="top:402px;font-size:19px">What we do</h2>
<p class="lead abs" style="top:436px">Lorem Ipsum has been the industry's standard dummy text ever since the 1500s, when an unknown printer took a gallepecimen book. It has t only five centuries, but also the leap into electronice the 1500s, when an unknown priley of tyke a type specimen book. It h as survived not only five centuries, but also the leap into electronic.</p>

<div class="feature abs" style="left:51px;top:510px">
  <div class="feature-icon"><svg width="30" height="30" viewBox="0 0 30 30" fill="none" stroke="#fff" stroke-width="2"><path d="M15 3v8M8 6l4 5M22 6l-4 5M6 13h18M9 17h12M15 17v10M10 22h10"/></svg></div>
  <div class="feature-title">Fast Work</div>
  <p class="feature-text">Lorem Ipsum has been the industry's standard dummyb survived not only five centuries, but also the leap into electronic typese.</p>
  <div class="read-more">Read More &gt;&gt;</div>
</div>
<div class="feature abs" style="left:310px;top:510px">
  <div class="feature-icon"><svg width="30" height="30" viewBox="0 0 30 30" fill="none" stroke="#fff" stroke-width="2"><ellipse cx="13" cy="6" rx="9" ry="3"/><path d="M4 6v12c0 2 4 3 9 3M22 6v5M4 12c0 2 4 3 9 3"/><rect x="15" y="15" width="11" height="11"/><path d="M15 20h11M20 15v11"/></svg></div>
  <div class="feature-title">Scalable</div>
  <p class="feature-text">Lorem Ipsum has been the industry's standard dummyb survived not only five centuries, but also the leap into electronic typese.</p>
  <div class="read-more">Read More &gt;&gt;</div>
</div>
<div class="feature abs" style="left:561px;top:510px">
  <div class="feature-icon"><svg width="30" height="30" viewBox="0 0 30 30" fill="none" stroke="#fff" stroke-width="2"><path d="M3 26h24M3 4v22M8 24v-8M12 24v-12M16 24v-9M20 24v-6M6 20L26 4"/></svg></div>
  <div class="feature-title">Built for Analytics</div>
  <p class="feature-text">Lorem Ipsum has been the industry's standard dummyb survived not only five centuries, but also the leap into electronic typese.</p>
  <div class="read-more">Read More &gt;&gt;</div>
</div>

<section class="markets abs" role="img" aria-label="Faint photo of business people over printed sales reports"></section>
<h2 class="section-title display abs" style="top:721px;font-size:17px">quenvo maps markets to drive sales and marketing</h2>
<p class="lead abs" style="top:756px;left:136px;width:547px">Lorem Ipsum has been the industry's standard dummy text ever since the 1500s, when an unknown printer took a galley of type and scrambled it to make a type specimen book. It has survived not only five centuries, but also the leap into electronic typeseter took a galley of type and scrambled it to make a type . It hasIso the leap into electronic typese.</p>

<h3 class="sub-title abs" style="left:99px;width:260px;top:812px">Our Application</h3>
<p class="sub-text abs" style="left:60px;width:340px;top:843px">As soon as you contact our expert team, this will be the only form you have to fill in!</p>
<h3 class="sub-title abs" style="left:458px;width:260px;top:812px">Get Started Now</h3>
<p class="sub-text abs" style="left:418px;width:340px;top:843px">As soon as you contact our expert team, this will be the only form you have to fill in!</p>

<div class="monitor abs">
  <div class="screen"><div class="screen-view" role="img" aria-label="Network graph of companies linked by coloured nodes"></div></div>
  <div class="stand"></div>
  <div class="base"></div>
</div>

<form class="form abs">
  <div class="form-head">100% PRIVACY GUARANTEED</div>
  <div class="field">TYPE YOUR NAME</div>
  <div class="field">EMAIL ADDRESS</div>
  <div class="field">PHONE NUMBER</div>
  <div class="field tall">TYPE YOUR MESSAGE</div>
  <div class="form-btn">REQUEST A CALL BACK</div>
</form>

<nav class="footer-nav abs"><span>Home</span><span>About us</span><span>Services</span><span>Data analytics</span><span>Contact us</span></nav>
<div class="social social-foot abs"><span></span><span></span><span></span><span></span><span></span></div>
<p class="copyright abs">© 2015 quenvo Inc. All rights reserved</p>

</body>
</html>
```